Stationery Design Project

We need, stationary designs for a store of children and juvenile furniture.
we have the logo. also need tags for the furniture with enought space to include description and options , maybe a 4" x 6" tag.

Target Market(s)

Parents of childrens and teens

Industry/Entity Type

Store

```html
<!DOCTYPE html>
<html lang="en">
<head>
<meta charset="utf-8">
<title>Little Oak Home Letterhead</title>
<link rel="stylesheet" href="https://fonts.googleapis.com/css2?family=Arimo:wght@400;700&display=swap">
<style>
  :root {
    --backdrop: #e4e4e4;
    --paper: #f7f7f7;
    --ink: #6a6a6a;
    --ink-soft: #8a8a8a;
    --teal: #5aa5ae;
    --slate: #6d6d6d;
  }
  * { margin: 0; padding: 0; box-sizing: border-box; }
  html, body {
    width: 1200px;
    height: 968px;
    overflow: hidden;
    background: var(--backdrop);
    font-family: "Arimo", Arial, sans-serif;
  }
  .canvas {
    position: relative;
    width: 1200px;
    height: 968px;
  }
  .letterhead {
    position: absolute;
    left: 273px;
    top: 24px;
    width: 654px;
    height: 920px;
    background: var(--paper);
    box-shadow: 0 2px 10px rgba(0,0,0,0.08);
    overflow: hidden;
  }
  .brand {
    position: absolute;
    top: 60px;
    left: 0;
    right: 0;
    display: flex;
    justify-content: center;
    align-items: center;
    gap: 10px;
  }
  .brand-mark {
    width: 18px;
    height: 18px;
    background: var(--teal);
  }
  .brand-name {
    font-size: 22px;
    font-weight: 700;
    letter-spacing: 0.5px;
    color: var(--ink);
    white-space: nowrap;
  }
  .contact {
    position: absolute;
    left: 48px;
    bottom: 62px;
    font-style: normal;
    font-size: 9px;
    line-height: 15px;
    color: var(--ink-soft);
    white-space: nowrap;
  }
  .contact .label { color: var(--teal); }
  .footer-bands {
    position: absolute;
    left: 0;
    right: 0;
    bottom: 0;
    height: 20px;
    display: flex;
  }
  .band-slate { width: 36%; background: var(--slate); }
  .band-gap { width: 6px; background: var(--paper); }
  .band-teal { flex: 1; background: var(--teal); }
</style>
</head>
<body>
  <main class="canvas">
    <section class="letterhead">
      <header class="brand">
        <span class="brand-mark"></span>
        <span class="brand-name">Little Oak Home</span>
      </header>

      <address class="contact">
        <p>Harbour Mill Road Westfield Park NSW 2790 · <span class="label">Tel:</span> +61 2 5550 1200 · <span class="label">Fax:</span> +61 2 5550 1210</p>
        <p><span class="label">Email:</span> hello@littleoakhome.com · www.littleoakhome.com</p>
      </address>

      <div class="footer-bands">
        <div class="band-slate"></div>
        <div class="band-gap"></div>
        <div class="band-teal"></div>
      </div>
    </section>
  </main>
</body>
</html>
```